Marlowby Services Website Design

We have most content but require a professional design. We have a logo already and will need it utilized along with several of the photos from the attached documentation.
First page should have our mission and Vision and the synapsis provided in the word document. Visitors will be prompted to select from one of our 3 divisions from this page.
Each division will have the same list of tabs : About, Services, Safety, Careers and Contact.
Photos on each divisions page should be representative of the divisions offerings. The word doc attached contains the requested content and we are open to edits that would complement and fill the website.
I like the Quorvane site www.quorvane.example - they are our competition so cant be modeled directly after this.
Please include prompts to request quote at each service page. align the format of the geotechnical page to the other 2 divisions.
I used chat gpt for some of the content so will need it optimized for SCO.

```html
<!DOCTYPE html>
<html lang="en">
<head>
<meta charset="utf-8">
<title>Marlowby Services</title>
<link href="https://fonts.googleapis.com/css2?family=Lato:wght@400;700;900&display=swap" rel="stylesheet">
<style>
:root{
  --red:#e8222a;
  --ink:#111111;
  --text:#333333;
  --muted:#444444;
  --grey-bg:#f5f5f5;
  --white:#ffffff;
  --black:#000000;
  --line:#e3e3e3;
}
*{box-sizing:border-box;margin:0;padding:0}
html,body{width:1200px;height:2671px;overflow:hidden}
body{position:relative;background:var(--white);font-family:'Lato',sans-serif;color:var(--text)}
.abs{position:absolute}
a{color:inherit;text-decoration:none}

/* header */
.site-header{left:0;top:0;width:1200px;height:70px;background:var(--white)}
.brand{left:141px;top:14px;font-weight:900;font-size:36px;letter-spacing:2px;color:var(--red);line-height:40px}
.main-nav{left:652px;top:24px;display:flex;gap:33px;font-size:13px;color:var(--ink)}
.btn{display:inline-flex;align-items:center;justify-content:center;background:var(--red);color:var(--white);font-size:13px;font-weight:700}
.nav-cta{left:953px;top:18px;width:106px;height:34px}

/* hero */
.hero{left:0;top:70px;width:1200px;height:565px;background:linear-gradient(180deg,#6f8a98 0%,#8a8d7c 18%,#8c7660 45%,#7a5f45 100%)}
.hero-photo{left:0;top:0;width:1200px;height:565px;background:radial-gradient(ellipse at 55% 45%,rgba(240,240,240,.55) 0%,rgba(240,240,240,.25) 35%,rgba(0,0,0,0) 60%)}
.hero-title{left:0;top:432px;width:1200px;text-align:center;color:var(--white);font-weight:700;font-size:33px}
.hero-sub{left:0;top:478px;width:1200px;text-align:center;color:var(--white);font-size:25px}

/* divisions */
.section-title{width:1200px;left:0;text-align:center;color:var(--ink);font-size:33px;font-weight:700}
.divisions-title{top:692px}
.division{top:755px;width:289px;height:350px}
.division-photo{left:0;top:0;width:289px;height:218px}
.division-body{left:14px;top:192px;width:261px;height:158px;background:var(--white);padding:15px 14px 0;border:1px solid transparent}
.division.featured .division-body{border-color:var(--red);box-shadow:0 6px 14px rgba(0,0,0,.12)}
.division h3{font-size:15px;font-weight:700;color:var(--ink);margin-bottom:8px}
.division p{font-size:11px;line-height:19px;color:var(--muted)}
.read-more{display:flex;align-items:center;gap:6px;margin-top:7px;font-size:12px;font-weight:700;color:var(--red)}

/* vision */
.about-band{left:0;top:1190px;width:1200px;height:512px;background:var(--grey-bg)}
.about-photo{left:141px;top:85px;width:438px;height:342px;background:linear-gradient(180deg,#4d5e46 0%,#8f9288 45%,#a8a296 70%,#9a948a 100%)}
.about-text{left:622px;top:82px;width:438px}
.about-text h2{font-size:21px;font-weight:700;color:var(--ink);margin-bottom:8px}
.about-text p{font-size:12px;line-height:21.6px;color:var(--text);margin-bottom:20px}
.about-cta{width:106px;height:35px;margin-top:-3px}

/* services */
.services-title{top:1781px}
.services-sub{left:0;top:1824px;width:1200px;text-align:center;font-size:12.5px;font-weight:700;color:var(--muted)}
.service{top:1885px;width:219px;height:123px;background:var(--white);border:1px solid var(--line);box-shadow:0 2px 6px rgba(0,0,0,.05);padding:48px 16px 0 18px}
.service-icon{left:24px;top:-21px;width:59px;height:59px;border-radius:50%;display:flex;align-items:center;justify-content:center}
.service-icon.red{background:var(--red)}
.service-icon.dark{background:var(--ink)}
.service h3{font-size:14px;font-weight:700;color:var(--ink);margin-bottom:6px}
.service p{font-size:10.5px;line-height:19px;color:var(--muted);padding-left:2px}
.services-cta{left:547px;top:2037px;width:106px;height:35px}

/* footer */
.site-footer{left:0;top:2340px;width:1200px;height:331px;background:var(--black)}
.promo-shadow{left:194px;top:2340px;width:812px;height:50px;background:#555}
.promo{left:184px;top:2155px;width:832px;height:226px;background:var(--grey-bg);box-shadow:0 0 20px rgba(0,0,0,.08);text-align:center;padding-top:36px}
.promo p{font-size:23px;font-weight:700;color:var(--ink);line-height:30.5px}
.promo .accent{color:var(--red)}
.promo-cta{width:106px;height:35px;margin-top:22px}
.footer-heading{font-size:18.5px;color:var(--white);padding-bottom:9px;border-bottom:1px solid #333;width:113px}
.footer-heading::after{content:"";display:block;width:36px;height:3px;background:var(--red);margin-top:-1px;position:relative;top:10px}
.quick{left:143px;top:2428px}
.contact{left:507px;top:2428px}
.contact .footer-heading{width:143px}
.links{left:143px;top:2480px;display:grid;grid-template-columns:127px 100px;row-gap:12px;font-size:12.5px;color:var(--white)}
.links li{list-style:none}
.links li::before{content:"»";margin-right:9px;font-size:11px}
.contact-item{left:507px;color:var(--white);font-size:12.5px;line-height:20px}
.contact-item strong{display:flex;align-items:center;gap:8px;font-weight:700}
.contact-item span{display:block;padding-left:21px}
.footer-brand{left:827px;top:2437px;font-weight:900;font-size:30px;letter-spacing:2px;color:var(--red)}
.address{left:827px;top:2473px;color:var(--white);font-size:12.5px;line-height:20px;display:flex;gap:8px}
.footer-rule{left:141px;top:2617px;width:918px;height:1px;background:#444}
.copyright{left:145px;top:2636px;font-size:12.5px;color:var(--white)}
.social{left:925px;top:2629px;display:flex;gap:7px}
.social span{width:28px;height:28px;border-radius:50%;background:var(--red);display:block}
</style>
</head>
<body>

<header class="abs site-header">
  <div class="abs brand">MARLOWBY</div>
  <nav class="abs main-nav"><a href="#">Home</a><a href="#">About Us</a><a href="#">Safety</a><a href="#">Careers</a></nav>
  <a class="abs btn nav-cta" href="#">Contact Us</a>
</header>

<section class="abs hero">
  <div class="abs hero-photo" role="img" aria-label="White aerial lift truck with extended boom parked on a gravel yard"></div>
  <h1 class="abs hero-title">Delivering Safe, Reliable Aerial Access &amp; Maintenance Services</h1>
  <p class="abs hero-sub">To Oil &amp; Gas,Construction, Utility, &amp; Renewable Energy Sector</p>
</section>

<h2 class="abs section-title divisions-title">Our Divisions</h2>

<article class="abs division" style="left:141px">
  <div class="abs division-photo" role="img" aria-label="Aerial lift boom reaching a wind turbine tower under blue sky" style="background:linear-gradient(180deg,#3d74c2 0%,#8db3e2 65%,#9a8a6c 100%)"></div>
  <div class="abs division-body">
    <h3>Aerial Access</h3>
    <p>Marlowby is a full-service wind energy service provider specializing in blade access &amp; repair, service and maintenance, and trouble shooting on most wind turbine platforms.</p>
    <a class="read-more" href="#">Read More <svg width="16" height="8" viewBox="0 0 16 8"><path d="M0 4h14M11 1l3 3-3 3" stroke="currentColor" stroke-width="1.5" fill="none"/></svg></a>
  </div>
</article>

<article class="abs division featured" style="left:455px">
  <div class="abs division-photo" role="img" aria-label="Red tracked drilling rig on a green hillside" style="background:linear-gradient(180deg,#1f3a2c 0%,#3f6a3a 50%,#2f4f2a 100%)"></div>
  <div class="abs division-body">
    <h3>Geotechnical Drilling</h3>
    <p>Lorem ipsum dolor amet conectetur adipising elit. Nullam porta turpis dui ut ultricies nisi sollicitudin et. Quisque vel tellus vitae mauris venenatis blandit.</p>
    <a class="read-more" href="#">Read More <svg width="16" height="8" viewBox="0 0 16 8"><path d="M0 4h14M11 1l3 3-3 3" stroke="currentColor" stroke-width="1.5" fill="none"/></svg></a>
  </div>
</article>

<article class="abs division" style="left:769px">
  <div class="abs division-photo" role="img" aria-label="White lift boom beside a wind turbine against blue sky" style="background:linear-gradient(160deg,#1f5fbf 0%,#4a86d8 60%,#7aa6e3 100%)"></div>
  <div class="abs division-body">
    <h3>Renewable Energy Services</h3>
    <p>Marlowby is a full-service wind energy service provider specializing in blade access &amp; repair, service and maintenance, and trouble shooting on most wind turbine platforms.</p>
    <a class="read-more" href="#">Read More <svg width="16" height="8" viewBox="0 0 16 8"><path d="M0 4h14M11 1l3 3-3 3" stroke="currentColor" stroke-width="1.5" fill="none"/></svg></a>
  </div>
</article>

<section class="abs about-band">
  <div class="abs about-photo" role="img" aria-label="Aerial lift truck parked on a gravel lot in front of trees"></div>
  <div class="abs about-text">
    <h2>Our Vision</h2>
    <p>To be the leading provider of aerial access, geotechnical drilling, and service solutions, setting the standard for excellence in safety, efficiency, and environmental stewardship.</p>
    <h2>Our Mission</h2>
    <p>At Marlowby, our mission is to deliver unparalleled aerial access, geotechnical drilling, and service and maintenance solutions, consistently exceeding our clients' expectations. We strive to achieve this by investing in cutting-edge technology, fostering a culture of safety and continuous improvement, and prioritizing environmental sustainability. Through collaboration, integrity, and dedication, we aim to contribute to the success of our clients while maintaining the highest standards of quality and professionalism.</p>
    <a class="btn about-cta" href="#">Contact Us</a>
  </div>
</section>

<h2 class="abs section-title services-title">Marlowby Services</h2>
<p class="abs services-sub">Delivering Safe Reliable Aerial Access And Maintenance Services</p>

<div class="abs service" style="left:141px">
  <div class="abs service-icon red"><svg width="30" height="30" viewBox="0 0 30 30" fill="none" stroke="#fff" stroke-width="1.5"><rect x="5" y="10" width="8" height="16"/><rect x="15" y="4" width="9" height="22"/><path d="M3 26h24"/></svg></div>
  <h3>Oil &amp; Gas</h3>
  <p>Lorem ipsum dolor sit amet coetetur adipiing egestas metus auctor elit.</p>
</div>
<div class="abs service" style="left:374px">
  <div class="abs service-icon dark"><svg width="30" height="30" viewBox="0 0 30 30" fill="none" stroke="#fff" stroke-width="1.5"><path d="M10 26L15 5l5 21M8 26h14M12 17h6M6 8h18"/></svg></div>
  <h3>Construction</h3>
  <p>Lorem ipsum dolor sit amet coetetur adipiing egestas metus auctor elit.</p>
</div>
<div class="abs service" style="left:607px">
  <div class="abs service-icon red"><svg width="30" height="30" viewBox="0 0 30 30" fill="none" stroke="#fff" stroke-width="1.5"><circle cx="15" cy="15" r="8"/><circle cx="15" cy="15" r="3"/><path d="M15 3v4M15 23v4M3 15h4M23 15h4"/></svg></div>
  <h3>Utility</h3>
  <p>Lorem ipsum dolor sit amet coetetur adipiing egestas metus auctor elit.</p>
</div>
<div class="abs service" style="left:840px">
  <div class="abs service-icon dark"><svg width="30" height="30" viewBox="0 0 30 30" fill="none" stroke="#fff" stroke-width="1.5"><path d="M6 15a9 9 0 0 1 15-7M24 15a9 9 0 0 1-15 7"/><path d="M15 20v-6c0-3 3-5 5-5 0 3-2 5-5 5"/></svg></div>
  <h3>Renewable Energy Industries</h3>
  <p>Lorem ipsum dolor sit amet coetetur adipiing egestas metus auctor elit.</p>
</div>
<a class="abs btn services-cta" href="#">Contact Us</a>

<footer class="abs site-footer"></footer>
<div class="abs promo-shadow"></div>
<section class="abs promo">
  <p><span class="accent">MARLOWBY</span> is a Full Service Wind Energy Service Provider<br>Specializing In Blade Access And Repair, Service And Maintenance,<br>And Trouble Shooting On Most Wind Turbine Platforms.</p>
  <a class="btn promo-cta" href="#">Contact Us</a>
</section>

<div class="abs quick"><h4 class="footer-heading" style="font-weight:400">Quick Links</h4></div>
<ul class="abs links">
  <li>Home</li><li>Safety</li><li>About</li><li>Careers</li><li>Services</li><li>Contact Us</li>
</ul>

<div class="abs contact"><h4 class="footer-heading" style="font-weight:400">Contact Details</h4></div>
<div class="abs contact-item" style="top:2481px">
  <strong><svg width="13" height="13" viewBox="0 0 24 24"><path fill="#fff" d="M6.6 10.8a15 15 0 0 0 6.6 6.6l2.2-2.2c.3-.3.7-.4 1-.2 1.1.4 2.3.6 3.6.6.6 0 1 .4 1 1V20c0 .6-.4 1-1 1A17 17 0 0 1 3 4c0-.6.4-1 1-1h3.5c.6 0 1 .4 1 1 0 1.3.2 2.5.6 3.6.1.3 0 .7-.2 1z"/></svg>Phone</strong>
  <span>(555)-014-2290</span>
</div>
<div class="abs contact-item" style="top:2532px">
  <strong><svg width="13" height="11" viewBox="0 0 24 18"><rect x="1" y="1" width="22" height="16" fill="#fff"/><path d="M1 1l11 9 11-9" stroke="#000" stroke-width="1.6" fill="none"/></svg>Email</strong>
  <span>careers@marlowbyservices.example</span>
</div>

<div class="abs footer-brand">MARLOWBY</div>
<div class="abs address">
  <svg width="12" height="15" viewBox="0 0 12 16"><path fill="#fff" d="M6 0a6 6 0 0 0-6 6c0 4.5 6 10 6 10s6-5.5 6-10a6 6 0 0 0-6-6zm0 8.5A2.5 2.5 0 1 1 6 3.5a2.5 2.5 0 0 1 0 5z"/></svg>
  <div>218 Birch Avenue Ridgefall<br>AB T0X-4B2</div>
</div>

<div class="abs footer-rule"></div>
<p class="abs copyright">© 2024 MARLOWBY. All Rights Reserved.</p>
<div class="abs social" aria-label="Social links"><span></span><span></span><span></span><span></span></div>

</body>
</html>
```